Design and Renovation Company Luxury Business Card

I want to create a luxury business card for a Design and Renovation Firm . We will use our current logo. The company name is 528BUILDA. We do not want anything standard. We need a very unique concept.
Please see uploaded inspiration. I really like the textured paper option. I would like the card to be thick with debossing, and/or embossing options. The logo has orange in it but I would like to see the card with and without the orange. I think the orange may make the company feel less high-end. The goal is to elevate the logo not match its vibe per se of the logo. We want something very unique, not standard at all!
I would like a space for :
Logo,
Name,
Position,
Email,
Office number,
Website Address,
Business Address,
Thank you!
Have fun!
Target Market(s)
Home owners Age 35 +
Industry/Entity Type
Design and Renovation
Contact Information for Business Card
Logo, Name, Position, Email, Office number, Website Address, Business Address,.
Colors
Designer to choose colors to be used in the design.
Requirements
Must have
- A luxury designer feel. Must be black or dark grey but open to other luxury ideas.
Nice to have
- Gold, silver, black embossing or debossing. Textured paper design.
Should not have
- A cheap look and feel.

```html
<!DOCTYPE html>
<html lang="en">
<head>
<meta charset="utf-8">
<title>528BUILDA Business Card</title>
<link href="https://fonts.googleapis.com/css2?family=Arimo:wght@400;700&display=swap" rel="stylesheet">
<style>
  :root {
    --backdrop: #9a9a9a;
    --card-front: #383838;
    --card-back: #2a2a2a;
    --ink-white: #f4f4f4;
    --ink-soft: #e6e6e6;
    --accent: #f0962a;
  }
  * { box-sizing: border-box; margin: 0; padding: 0; }
  html, body { width: 1200px; height: 1050px; overflow: hidden; }
  body {
    background: var(--backdrop);
    font-family: "Arimo", Arial, sans-serif;
    position: relative;
  }
  .card {
    position: absolute;
    left: 250px;
    width: 700px;
    height: 400px;
    border-radius: 22px;
    box-shadow: 0 10px 28px rgba(0,0,0,0.28);
  }
  .card--front { top: 90px; background: var(--card-front); }
  .card--back  { top: 560px; background: var(--card-back); }

  /* front */
  .contact {
    position: absolute;
    left: 60px;
    bottom: 62px;
    color: var(--ink-soft);
    font-size: 17px;
    line-height: 1.3;
  }
  .contact__name {
    color: var(--accent);
    font-weight: 700;
    font-size: 27px;
    line-height: 1.1;
  }
  .contact__email { margin-bottom: 12px; }
  .divider {
    position: absolute;
    left: 370px;
    bottom: 58px;
    width: 1.5px;
    height: 68px;
    background: var(--ink-soft);
  }
  .lines {
    position: absolute;
    left: 392px;
    bottom: 62px;
    color: var(--ink-soft);
    font-size: 17px;
    line-height: 1.55;
  }
  .lines__row { display: flex; align-items: center; gap: 9px; }
  .lines__row svg { width: 14px; height: 14px; flex: none; }
  .front-mark {
    position: absolute;
    right: 62px;
    top: 70px;
    display: flex;
    flex-direction: column;
    align-items: flex-end;
    gap: 16px;
  }
  .front-mark__square { width: 96px; height: 96px; background: var(--accent); }
  .front-mark__name {
    color: var(--ink-white);
    font-weight: 700;
    font-size: 24px;
    letter-spacing: 1px;
  }

  /* back */
  .brand {
    position: absolute;
    left: 0; right: 0;
    top: 125px;
    display: flex;
    flex-direction: column;
    align-items: center;
  }
  .brand__row { display: flex; align-items: center; gap: 18px; }
  .brand__square { width: 46px; height: 46px; background: var(--accent); }
  .brand__name {
    color: var(--ink-white);
    font-weight: 700;
    font-size: 68px;
    letter-spacing: 3px;
    line-height: 1;
  }
  .brand__tagline {
    margin-top: 14px;
    color: var(--ink-white);
    font-weight: 700;
    font-size: 15px;
    letter-spacing: 7px;
    padding-left: 64px;
  }
</style>
</head>
<body>
  <section class="card card--front">
    <div class="contact">
      <div class="contact__name">Marcus Hale</div>
      <div class="contact__role">President</div>
      <div class="contact__email">name@528BUILDA.com</div>
      <div class="contact__address">4127 Harlow Avenue<br>Glen Ridge, NJ 07028</div>
    </div>
    <div class="divider"></div>
    <div class="lines">
      <div class="lines__row">
        <svg viewBox="0 0 24 24" aria-hidden="true"><path fill="#f0962a" d="M6.6 10.8a15 15 0 0 0 6.6 6.6l2.2-2.2a1 1 0 0 1 1-.25 11.4 11.4 0 0 0 3.6.57 1 1 0 0 1 1 1V20a1 1 0 0 1-1 1A17 17 0 0 1 3 4a1 1 0 0 1 1-1h3.5a1 1 0 0 1 1 1c0 1.25.2 2.45.57 3.57a1 1 0 0 1-.25 1z"/></svg>
        <span>(555) 0184-3927</span>
      </div>
      <div class="lines__row">
        <svg viewBox="0 0 24 24" aria-hidden="true"><circle cx="12" cy="12" r="10" fill="none" stroke="#f0962a" stroke-width="2.4"/><path d="M2 12h20M12 2c3 3 3 17 0 20M12 2c-3 3-3 17 0 20" fill="none" stroke="#f0962a" stroke-width="2"/></svg>
        <span>www.528BUILDA.com</span>
      </div>
    </div>
    <div class="front-mark">
      <div class="front-mark__square"></div>
      <div class="front-mark__name">528BUILDA</div>
    </div>
  </section>

  <section class="card card--back">
    <div class="brand">
      <div class="brand__row">
        <div class="brand__square"></div>
        <div class="brand__name">528BUILDA</div>
      </div>
      <div class="brand__tagline">Design and Renovation Firm</div>
    </div>
  </section>
</body>
</html>
```